Wordpress Design for a Digital Management Consulting Business

I need a simple Wordpress Design and someone to set it up for a new boutique management consulting business called Quillon Advisory that specialises in providing strategic advice to help grow digital businesses. It covers business strategy, marketing strategy, digital strategy, web product development, marketing campaigns, social, search, etc. From strategy to implementation.

URL is: quillonadvisory.com.au

My professional background is here: au.linkedin.com/in/hollyprenwick

Competitors: other boutique digital/marketing management consulting businesses in Australia

The logos, colours and fonts are attached.

I would like the site to convey a business that is Smart/intelligent, Contemporary, Progressive, Digital, Energetic, Friendly.

The objective of the site is to educate visitors about what Quillon Advisory does and encourage them to contact me for more information. It will be very light on content.

Target Market(s)

CEOs/Managing Directors, General Managers, Marketing Directors

Industry/Entity Type

Management Consulting

Font styles to use
Sans Serif

Colors
e34197
5c5c5c
000000

Requirements
Must have
• Site design requirements:
• Choose an appropriate Wordpress template, set it up for me and let me be able to edit it ongoing.
• It should use lots of images - these can be inspirational and not necessarily tied directly to the work
• Pink should feature, but not be the dominant colour.
• Site structure should be:
• 1. Home page - image led with horizontal navigation. Text beneath and images to describe the services.
• 2. About page - with space to write text and insert a picture of the Director
• 3. Services - with space to highlight services either as a list or graphically with text
• 4. Contact page - with space to write text and add email links, etc.
• Should have horizontal navigation
• It should have the flexibility to add another page
Nice to have
• Use the tree icon somehow in the design - consider in the background enlarged
• Use pink, grey, black from logo. Can introduce another complimentary colour if necessary.
• Can introduce another complimentary font to go with the logo font.
Should not have
• Use cliched business images and icons, eg. business suits, hand shakes, business men, business ties.

```html
<!DOCTYPE html>
<html lang="en">
<head>
<meta charset="utf-8">
<title>Quillon Advisory</title>
<link href="https://fonts.googleapis.com/css2?family=Raleway:wght@300;400;500;600;700;800&display=swap" rel="stylesheet">
<style>
:root{
  --pink:#e34197;
  --grey:#5c5c5c;
  --black:#000000;
  --ink:#333333;
  --light:#f1f1f1;
  --footer:#1e1e1e;
  --footer-text:#bdbdbd;
  --white:#ffffff;
}
*{margin:0;padding:0;box-sizing:border-box}
html,body{width:1200px;height:2264px;overflow:hidden}
body{font-family:'Raleway',sans-serif;color:var(--grey);background:var(--white);position:relative}
.site-header{position:absolute;left:0;top:0;width:1200px;height:88px;background:var(--white)}
.brand{position:absolute;left:60px;top:28px}
.brand-name{font-size:26px;font-weight:600;color:var(--pink);letter-spacing:1px;line-height:1}
.main-nav{position:absolute;right:60px;top:36px;display:flex;gap:34px}
.main-nav a{font-size:14px;font-weight:600;color:var(--grey);text-decoration:none;letter-spacing:1px;position:relative;padding-top:10px}
.main-nav a.active{color:var(--black)}
.main-nav a.active::before{content:"";position:absolute;left:-8px;right:-8px;top:-4px;height:3px;background:var(--pink)}
.main-nav a.active::after{content:"";position:absolute;left:-8px;right:-8px;bottom:-8px;height:1px;background:#ccc}
.hero{position:absolute;left:0;top:88px;width:1200px;height:452px}
.hero-photo{position:absolute;inset:0;background:linear-gradient(100deg,#6a6a6a 0%,#9a9a9a 35%,#c9c9c9 60%,#e6e6e6 100%)}
.hero-shade{position:absolute;inset:0;background:linear-gradient(90deg,rgba(0,0,0,.45),rgba(0,0,0,0) 55%)}
.hero-copy{position:absolute;left:100px;top:130px;width:440px}
.hero-title{font-size:78px;font-weight:800;color:var(--pink);letter-spacing:3px;line-height:1}
.hero-sub{font-size:17px;font-weight:700;color:var(--white);letter-spacing:.5px;margin-top:8px}
.hero-text{font-size:14px;color:var(--white);line-height:1.45;margin-top:18px}
.btn-dark{display:inline-block;margin-top:20px;background:#3a3a3a;color:var(--white);font-size:15px;padding:10px 26px;text-decoration:none}
.hero-arrow{position:absolute;top:200px;width:20px;height:40px}
.hero-dots{position:absolute;left:0;right:0;top:424px;display:flex;justify-content:center;gap:8px}
.hero-dots span{width:13px;height:13px;border-radius:50%;background:var(--white);opacity:.8}
.hero-dots span.on{background:#444;opacity:1}
.section-title{position:absolute;left:0;width:1200px;display:flex;align-items:center;justify-content:center;gap:18px;color:var(--pink);font-size:24px;font-weight:500;letter-spacing:2px}
.section-title.dark{color:var(--grey)}
.section-title::before,.section-title::after{content:"";width:110px;height:1px;background:#999}
.section-title .underline{position:absolute;top:40px;left:50%;width:60px;margin-left:-30px;height:2px;background:var(--pink)}
.who-text{position:absolute;left:54px;top:656px;width:1092px;font-size:17px;line-height:1.6;color:var(--grey)}
.btn-outline{position:absolute;border:2px solid var(--pink);color:var(--pink);font-size:18px;text-decoration:none;text-align:center;background:var(--white)}
.services{position:absolute;left:0;top:912px;width:1200px;height:588px;background:var(--light)}
.service{position:absolute;top:116px;width:300px;text-align:center}
.service-photo{width:268px;height:166px;margin:0 auto}
.service h3{font-size:21px;font-weight:600;color:var(--pink);margin-top:48px;letter-spacing:.3px;white-space:nowrap}
.service p{font-size:15px;line-height:1.4;margin:12px auto 0;width:268px;color:var(--grey)}
.service .btn-small{display:inline-block;border:2px solid var(--pink);background:var(--white);color:var(--ink);font-size:14px;padding:8px 18px;text-decoration:none}
.service .btn-wrap{position:absolute;top:396px;left:0;right:0}
.what{position:absolute;left:0;top:1500px;width:1200px;height:468px;background:linear-gradient(180deg,#fafafa,#ececec 60%,#f6f6f6)}
.what-item{position:absolute;top:128px;width:340px;text-align:center}
.what-icon{width:96px;height:96px;border-radius:50%;background:var(--pink);margin:0 auto;display:flex;align-items:center;justify-content:center}
.what-item h3{font-size:21px;font-weight:600;color:var(--black);margin-top:24px;white-space:nowrap}
.what-item p{font-size:15px;line-height:1.4;margin:12px auto 0;width:240px;text-align:left;color:var(--ink)}
.site-footer{position:absolute;left:0;top:1968px;width:1200px;height:296px;background:var(--footer);color:var(--footer-text)}
.foot-col{position:absolute;top:32px}
.foot-col h4{font-size:22px;font-weight:400;color:var(--white);letter-spacing:.5px}
.foot-col hr{border:0;border-top:1px solid #555;margin:12px 0 16px}
.foot-col ul{list-style:none}
.foot-col li{font-size:13px;line-height:26px;padding-left:14px;position:relative}
.foot-col li::before{content:"";position:absolute;left:0;top:11px;width:4px;height:4px;border-radius:50%;background:var(--footer-text)}
.social{display:flex;flex-direction:column;gap:12px;margin-left:14px}
.social span{width:26px;height:26px;border-radius:50%;background:#7a7a7a}
.contact p{font-size:13px;line-height:1.5}
.contact .line{display:flex;align-items:center;gap:10px;margin-top:12px;font-size:13px}
.contact .ico{width:22px;height:22px;border-radius:50%;background:#7a7a7a;display:flex;align-items:center;justify-content:center}
</style>
</head>
<body>

<header class="site-header">
  <div class="brand"><span class="brand-name">QUILLON ADVISORY</span></div>
  <nav class="main-nav">
    <a href="#" class="active">HOME</a>
    <a href="#">ABOUT US</a>
    <a href="#">SERVICES</a>
    <a href="#">PROJECTS</a>
    <a href="#">NEWS</a>
    <a href="#">CONTACT</a>
  </nav>
</header>

<section class="hero">
  <div class="hero-photo" role="img" aria-label="Photograph of a bright modern office workspace with a laptop on a desk"></div>
  <div class="hero-shade"></div>
  <svg class="hero-arrow" style="left:22px" viewBox="0 0 20 40"><path d="M16 4 L4 20 L16 36" fill="none" stroke="#fff" stroke-width="3"/></svg>
  <svg class="hero-arrow" style="right:22px" viewBox="0 0 20 40"><path d="M4 4 L16 20 L4 36" fill="none" stroke="#fff" stroke-width="3"/></svg>
  <div class="hero-copy">
    <div class="hero-title">ACHIEVE</div>
    <div class="hero-sub">YOUR GOALS AND LONG TERM SUCCESS</div>
    <p class="hero-text">Focused strategy, clear planning and hands-on delivery help growing digital businesses reach new markets, build stronger products and turn bold ideas into lasting results.</p>
    <a href="#" class="btn-dark">Read More</a>
  </div>
  <div class="hero-dots"><span class="on"></span><span></span><span></span><span></span></div>
</section>

<h2 class="section-title" style="top:584px">WHO WE ARE<span class="underline"></span></h2>
<p class="who-text">Quillon Advisory is a boutique management consulting company advising businesses in the digital, ecommerce, media, travel, technology and finance sectors on business, product and marketing strategy. Combining strategic thinking with digital knowhow and marketing expertise, Quillon Advisory works with businesses looking to accelerate growth, diversify or increase profit of a new or existing digital business.</p>
<a href="#" class="btn-outline" style="left:476px;top:802px;width:228px;height:52px;line-height:48px">Click to know more.</a>

<section class="services">
  <h2 class="section-title dark" style="top:50px">OUR SERVICES</h2>

  <div class="service" style="left:50px">
    <div class="service-photo" role="img" aria-label="Photograph of a hand touching a glowing digital interface" style="background:linear-gradient(135deg,#2b3440,#6b7c8e 60%,#b7c3cf)"></div>
    <h3>DIGITAL STRATEGY</h3>
    <p>With over 15 years experience in digital businesses, Quillon Advisory develops business, product, sales &amp; marketing strategies with a focus on accelerating or establishing digital businesses.</p>
    <div class="btn-wrap"><a href="#" class="btn-small">Read More</a></div>
  </div>

  <div class="service" style="left:450px">
    <div class="service-photo" role="img" aria-label="Illustration of a person sketching marketing charts on a whiteboard" style="background:linear-gradient(135deg,#e9eef2,#c9d6df 55%,#a9bccb)"></div>
    <h3>MARKETING STRATEGY</h3>
    <p>Whether you have a new product or want to accelerate growth of an existing business, Quillon Advisory can define a robust marketing strategy, and implement a successful marketing campaign.</p>
    <div class="btn-wrap"><a href="#" class="btn-small">Read More</a></div>
  </div>

  <div class="service" style="left:850px">
    <div class="service-photo" role="img" aria-label="Photograph of hands using a tablet with a laptop in soft light" style="background:linear-gradient(135deg,#d9c2b0,#a88f80 55%,#6f5f57)"></div>
    <h3>DIGITAL TRANSFORMATION</h3>
    <p>Quillon Advisory works with businesses to create a digital competitive advantage, identifying new opportunities and building digital capabilities.</p>
    <div class="btn-wrap"><a href="#" class="btn-small">Read More</a></div>
  </div>
</section>

<section class="what" role="img" aria-label="Faint background photograph of an office meeting table">
  <h2 class="section-title" style="top:32px">WHAT WE DO</h2>

  <div class="what-item" style="left:6px">
    <div class="what-icon">
      <svg width="50" height="50" viewBox="0 0 50 50"><path d="M25 6a13 13 0 0 0-8 23v6h16v-6a13 13 0 0 0-8-23z" fill="none" stroke="#fff" stroke-width="3"/><rect x="18" y="38" width="14" height="3" fill="#fff"/><rect x="20" y="43" width="10" height="3" fill="#fff"/></svg>
    </div>
    <h3>Strategic Thinking</h3>
    <p>Loremipsum dolor sit amet, consect eturadip iscingelit, sed do eius mod tempoinci, I dol velidit aboreetdolore magna aliqua.</p>
  </div>

  <div class="what-item" style="left:430px">
    <div class="what-icon">
      <svg width="52" height="52" viewBox="0 0 52 52"><rect x="8" y="30" width="8" height="14" fill="#fff"/><rect x="20" y="22" width="8" height="22" fill="#fff"/><rect x="32" y="14" width="8" height="30" fill="#fff"/><path d="M8 24 L22 14 L30 18 L44 6" fill="none" stroke="#fff" stroke-width="3"/></svg>
    </div>
    <h3>Analytical Approach</h3>
    <p>Loremipsum dolor sit amet, consect eturadip iscingelit, sed do eius mod tempoinci, I dol velidit aboreetdolore magna aliqua.</p>
  </div>

  <div class="what-item" style="left:822px">
    <div class="what-icon">
      <svg width="52" height="52" viewBox="0 0 52 52"><circle cx="26" cy="14" r="6" fill="#fff"/><circle cx="12" cy="36" r="6" fill="#fff"/><circle cx="40" cy="36" r="6" fill="#fff"/><path d="M22 19 L15 31 M30 19 L37 31 M18 38 L34 38" stroke="#fff" stroke-width="3"/></svg>
    </div>
    <h3>End to End Project Management</h3>
    <p>Loremipsum dolor sit amet, consect eturadip iscingelit, sed do eius mod tempoinci, I dol velidit aboreetdolore magna aliqua.</p>
  </div>
</section>

<footer class="site-footer">
  <div class="foot-col" style="left:44px;width:180px">
    <h4>Quick Links</h4><hr>
    <ul><li>Home</li><li>About Us</li><li>Projects</li><li>News</li><li>Contact</li></ul>
  </div>
  <div class="foot-col" style="left:252px;width:400px">
    <h4>Services</h4><hr>
    <div style="display:flex;gap:40px">
      <ul><li>Business Strategy</li><li>Digital Strategy</li><li>Marketing Strategy</li><li>Product Strategy</li><li>Marketing Campaigns</li></ul>
      <ul><li>Product Management</li><li>Digital Marketing</li><li>Digital CRM Strategy</li><li>Content Marketing</li><li>New Product Launches</li></ul>
    </div>
  </div>
  <div class="foot-col" style="left:716px;width:150px">
    <h4>Follow Us</h4><hr>
    <div class="social" aria-label="Social links"><span></span><span></span><span></span><span></span></div>
  </div>
  <div class="foot-col contact" style="left:898px;width:260px">
    <h4>Contact Details</h4><hr>
    <p>For more information about what we do, please contact:</p>
    <p style="margin-top:12px">Holly Prenwick</p>
    <div class="line"><span class="ico"><svg width="12" height="12" viewBox="0 0 12 12"><path d="M2 1 L4 1 L5 4 L3.5 5 A7 7 0 0 0 7 8.5 L8 7 L11 8 L11 10 A1 1 0 0 1 10 11 A9 9 0 0 1 1 2 A1 1 0 0 1 2 1z" fill="#222"/></svg></span>0412 555 018</div>
    <div class="line"><span class="ico"><svg width="12" height="10" viewBox="0 0 12 10"><rect x="0.5" y="0.5" width="11" height="9" fill="none" stroke="#222"/><path d="M0.5 0.5 L6 5 L11.5 0.5" fill="none" stroke="#222"/></svg></span>holly@quillonadvisory.com.au</div>
  </div>
</footer>

</body>
</html>
```